Corporate Business Card

Very professional, Modern, Not to busy, include phone address email, website
(253) 617-4930, 18761 52nd Avenue S, Kent, WA 98047, martin@plumlinegroup.com, varkoworks.com

Target Market(s)

Manufacturing

Industry/Entity Type

Aero, machining, manufacturing, Off road racing

Contact Information for Business Card

Phone, address email, website

```html
<!DOCTYPE html>
<html lang="en">
<head>
<meta charset="utf-8">
<title>Varko Works – Business Card</title>
<link rel="stylesheet" href="https://fonts.googleapis.com/css2?family=Arimo:wght@400;700&display=swap">
<style>
  :root {
    --backdrop: #e6e6e4;
    --card: #363636;
    --card-deep: #2c2c2c;
    --white: #ffffff;
    --red: #c8161b;
    --muted: #8a8a8a;
    --emboss: #262626;
  }
  * { margin: 0; padding: 0; box-sizing: border-box; }
  html, body { width: 1200px; height: 801px; overflow: hidden; }
  body {
    background: var(--backdrop);
    font-family: "Arimo", Arial, sans-serif;
    position: relative;
  }
  .card {
    position: absolute;
    top: 246px;
    width: 540px;
    height: 309px;
    background: var(--card);
    overflow: hidden;
    box-shadow: 0 6px 18px rgba(0,0,0,0.18);
  }
  .card--front { left: 45px; }
  .card--back { left: 615px; }

  .brand-name {
    position: absolute;
    left: 44px;
    top: 44px;
    color: var(--white);
    font-weight: 700;
    font-size: 50px;
    letter-spacing: 1px;
    text-transform: uppercase;
    line-height: 1;
  }
  .brand-rule {
    position: absolute;
    left: 44px;
    top: 122px;
    width: 260px;
    height: 1.5px;
    background: var(--white);
  }
  .person {
    position: absolute;
    left: 44px;
    top: 150px;
    text-align: right;
    width: 230px;
  }
  .person__name {
    color: var(--red);
    font-size: 20px;
    letter-spacing: 0.5px;
    text-transform: uppercase;
  }
  .person__title {
    color: var(--white);
    font-size: 14px;
    margin-top: 3px;
  }
  .divider {
    position: absolute;
    left: 292px;
    top: 146px;
    width: 1.5px;
    height: 72px;
    background: var(--muted);
  }
  .contacts {
    position: absolute;
    left: 308px;
    top: 146px;
    list-style: none;
  }
  .contacts li {
    display: flex;
    align-items: center;
    gap: 8px;
    color: var(--white);
    font-size: 13px;
    height: 24px;
  }
  .contacts svg { width: 12px; height: 12px; flex: none; }
  .address-band {
    position: absolute;
    left: 0;
    bottom: 20px;
    width: 540px;
    height: 34px;
  }
  .address-band__text {
    position: absolute;
    left: 110px;
    width: 320px;
    top: 0;
    line-height: 34px;
    text-align: center;
    color: var(--white);
    font-size: 15px;
  }

  .back-brand {
    position: absolute;
    left: 0;
    width: 540px;
    top: 118px;
    text-align: center;
    color: var(--emboss);
    font-weight: 700;
    font-size: 54px;
    letter-spacing: 1px;
    text-transform: uppercase;
    line-height: 1;
  }
  .back-rule {
    position: absolute;
    left: 90px;
    top: 192px;
    width: 190px;
    height: 1.5px;
    background: var(--emboss);
  }
</style>
</head>
<body>
  <section class="card card--front" aria-label="Business card front">
    <div class="brand-name">Varko Works</div>
    <div class="brand-rule"></div>

    <div class="person">
      <div class="person__name">Daniel Harper</div>
      <div class="person__title">Manager</div>
    </div>

    <div class="divider"></div>

    <ul class="contacts">
      <li>
        <svg viewBox="0 0 12 12" aria-hidden="true"><path d="M3 1 L5 3.5 L4 4.8 Q5 7 7.2 8 L8.5 7 L11 9 L9.8 11 Q4 10.5 1 3 Z" fill="#c8161b"/></svg>
        (253) 617-4930
      </li>
      <li>
        <svg viewBox="0 0 12 12" aria-hidden="true"><rect x="0.5" y="2.5" width="11" height="7.5" fill="#c8161b"/><path d="M0.5 2.5 L6 7 L11.5 2.5" stroke="#363636" stroke-width="1" fill="none"/></svg>
        martin@plumlinegroup.com
      </li>
      <li>
        <svg viewBox="0 0 12 12" aria-hidden="true"><circle cx="6" cy="6" r="5.5" fill="#c8161b"/><ellipse cx="6" cy="6" rx="2.2" ry="5.5" stroke="#363636" stroke-width="0.9" fill="none"/><line x1="0.5" y1="6" x2="11.5" y2="6" stroke="#363636" stroke-width="0.9"/></svg>
        www.varkoworks.com
      </li>
    </ul>

    <div class="address-band">
      <svg width="540" height="34" viewBox="0 0 540 34" aria-hidden="true">
        <polygon points="0,0 88,0 70,34 0,34" fill="#ffffff"/>
        <polygon points="96,0 448,0 430,34 78,34" fill="#c8161b"/>
        <polygon points="456,0 540,0 540,34 438,34" fill="#ffffff"/>
      </svg>
      <div class="address-band__text">18761 52nd Avenue S, Kent, WA 98047</div>
    </div>
  </section>

  <section class="card card--back" aria-label="Business card back">
    <div class="back-brand">Varko Works</div>
    <div class="back-rule"></div>
  </section>
</body>
</html>
```